2 x Digitize Logo | 2 x Business Cards | 2 x Fridge Magnets

We require 6 deliverables:
1. Residential logo redrawn (same just high quality for large print format).
2. Corporate logo redrawn (minor changes to wording and high quality for large print format).
3. New business card design for Furniture Removals (residential)
4. New business card design for Corporate Relocations (business)
5. New Fridge magnet for Furniture removals (residential)
6. New fridge magnet for Corporate Relocations (business)
1. Residential Logo
a. We require the logo to be translated into a high quality digital image with no modifications.
(see attached resilogo.jpg)
2. Residential Logo
a. We require the logo to be edited (add the word corporate relocations) be translated into a high quality digital image.
(see attached corplogo.jpg)
3. Using the resilogo please make a new business card for our business.
a. Please see the web site https://www.larkbendcarters.com.au for colours and inspiration.
b. The residential business card needs the following information:
i. Business Name (using the residential logo).
ii. Free Call: 1800 LB Cart (the L, B and Cart much be the same colour as the logo).
iii. Website: www.LarkbendCarters.com.au
iv. Address: 4/17 Ormsdale Court, VIC 3264
v. Email: cart@LarkbendCarters.com.au
vi. backof Card:
Review our service
www.PennantOrbit.com.au
Services: Local, Country, Interstate | Furniture Removals | Piano, Billiard Tables & Antiques
4. Using the corplogo please make a new business card for our business.
b. The corporate business card needs the following information:
i. Business Name (using the corporate logo).
v. Email: corporate@LarkbendCarters.com.au
vi. Back of Card:
Review our service
www.PennantOrbit.com.au
Services: Corporate relocations | Office equipment moves | Packing Service | Packing Materials
5. Using the resilogo please make a new fridge magent for our business.
b. The residential fidge magnet needs the following information:
iv. Services: Local, Country, Interstate | Furniture Removals | Piano, Billiard Tables & Antiques
6. Using the corplogo please make a new fridge magent for our business.
b. The corporate fidge magnet needs the following information:
iv. Services: Local, Country, Interstate | Corporate relocations
Target Market(s)
Residential Furniture Removals and Corporate Office relocations
Industry/Entity Type
Business
Contact Information for Business Card
Please see full brief for six items required
Requirements
Must have
- Clean simple, easy to read
Nice to have
- fresh, stand out, eye catching
Should not have
- plain, standard, boring, general

```html
<!DOCTYPE html>
<html lang="en">
<head>
<meta charset="utf-8">
<title>Larkbend Carters – Corporate Relocations Business Cards</title>
<link rel="stylesheet" href="https://fonts.googleapis.com/css2?family=Tinos:wght@700&family=Source+Sans+3:ital,wght@0,400;1,400&display=swap">
<style>
  :root {
    --brand-red: #c0141c;
    --brand-green: #08733a;
    --card-white: #ffffff;
    --card-back: #f2f2f2;
    --ink: #2a2a2a;
    --canvas: #e6e4e1;
  }
  * { box-sizing: border-box; margin: 0; padding: 0; }
  html, body {
    width: 1200px; height: 900px; overflow: hidden;
    background: var(--canvas);
    font-family: "Source Sans 3", "Myriad Pro", Arial, sans-serif;
  }
  .canvas { position: relative; width: 1200px; height: 900px; }

  .card { position: absolute; overflow: hidden; box-shadow: 0 4px 14px rgba(0,0,0,.18); }
  .card-front { left: 107px; top: 35px; width: 590px; height: 362px; background: var(--card-white); }
  .card-back  { left: 389px; top: 506px; width: 565px; height: 350px; background: var(--card-back); }

  .card-bands { position: absolute; inset: 0; width: 100%; height: 100%; }
  .band-red { fill: var(--brand-red); }
  .band-green { fill: var(--brand-green); }

  .brand-name {
    position: absolute; left: 0; width: 100%; text-align: center;
    font-family: "Tinos", "Times New Roman", serif; font-weight: 700;
    color: var(--brand-red); letter-spacing: -0.5px;
  }
  .brand-division {
    position: absolute; left: 0; width: 100%; text-align: center;
    color: var(--brand-green); font-weight: 400;
  }
  .card-front .brand-name { top: 52px; font-size: 35px; left: -14px; }
  .card-front .brand-division { top: 98px; font-size: 31px; left: -14px; }

  .contact-list { position: absolute; left: 24px; top: 253px; list-style: none; color: #fff; font-size: 18px; }
  .contact-list li { display: flex; align-items: center; height: 24.5px; }
  .contact-icon { width: 13px; height: 13px; margin-right: 8px; fill: #fff; }
  .contact-address {
    position: absolute; right: 40px; top: 277px; text-align: right;
    color: #fff; font-size: 18px; line-height: 24.5px; font-style: normal;
  }

  .card-back .brand-name { top: 90px; font-size: 19px; }
  .card-back .brand-division { top: 115px; font-size: 17px; }
  .review { position: absolute; left: 0; width: 100%; top: 219px; text-align: center; color: var(--ink); font-size: 15px; line-height: 22px; }
  .review em { font-style: italic; }
  .services-band {
    position: absolute; left: 0; bottom: 0; width: 100%; height: 77px;
    background: var(--brand-green); color: #fff; font-size: 15.5px;
    display: flex; flex-direction: column; justify-content: center; align-items: center; line-height: 21px;
  }
  .services-band span + span::before { content: "|"; margin: 0 9px; }
</style>
</head>
<body>
<main class="canvas">

  <section class="card card-front" aria-label="Business card front">
    <svg class="card-bands" viewBox="0 0 590 362" aria-hidden="true">
      <polygon class="band-red" points="0,184 396,184 376,209 0,209"/>
      <polygon class="band-green" points="410,177 590,177 590,362 0,362 0,213 384,213"/>
    </svg>
    <h1 class="brand-name">LARKBEND CARTERS</h1>
    <p class="brand-division">CORPORATE RELOCATIONS</p>
    <ul class="contact-list">
      <li><svg class="contact-icon" viewBox="0 0 16 16"><path d="M3.6 1.2l2.3 2.6-1.3 2.1c.9 2 2.4 3.6 4.4 4.6l2.1-1.3 2.7 2.3-1 2.6C7 14.1 1.8 9 1 2.2z"/></svg>1800 LB Cart</li>
      <li><svg class="contact-icon" viewBox="0 0 16 16"><path d="M1 3h14v10H1z M2 4.2v.6l6 4 6-4v-.6z" fill-rule="evenodd"/></svg>cart@LarkbendCarters.com.au</li>
      <li><svg class="contact-icon" viewBox="0 0 16 16"><circle cx="8" cy="8" r="7"/><path d="M8 1.5c-2 2-2 11 0 13M8 1.5c2 2 2 11 0 13M1.5 8h13" stroke="#08733a" stroke-width="1.1" fill="none"/></svg>www.LarkbendCarters.com.au</li>
    </ul>
    <address class="contact-address">4/17 Ormsdale Court,<br>VIC 3264</address>
  </section>

  <section class="card card-back" aria-label="Business card back">
    <h2 class="brand-name">LARKBEND CARTERS</h2>
    <p class="brand-division">CORPORATE RELOCATIONS</p>
    <p class="review"><em>Review our service</em><br>www.PennantOrbit.com.au</p>
    <div class="services-band">
      <div><span>Corporate relocations</span><span>Office equipment moves</span></div>
      <div><span>Packing Service</span><span>Packing Materials</span></div>
    </div>
  </section>

</main>
</body>
</html>
```